Tablet App design for business management system

TaskOra is a business management system made especially for service based businesses (our subscribers). It enables systemising your service businesses. This can be used by diverse industries like automotive service, beauty (hair salons, nail spas), Spas, Chiropractor, acupuntcure, osteo, yoga studio, business coach, etc.

The UI of the app needs to be designed using flat and clean UI design trends that are currently prevailing for B2C apps. Even the sliding menu panel can be removed and alternative placement of this functionality can be suggested. The color palette used for the design should be limited (3-5 colours)

The Current UI screens are open to suggestions for change. For ease of management in minimum steps, consolidation of functionality on different screens can be suggested, accompanies by a rational reason with the objective of having a simple and straight forward user experience.

User should be able to move from one function to another (booking > view appointments > profile) in no more than 1 or max 2 gestures.

Target Market(s)

SME businesses that provide time based services

Industry/Entity Type

Business

Font styles to use
Sans Serif

Requirements
Must have
• The power point slides give a detailed account of the process flow and functionality that the app is to follow.
• Reference this slide to ensure that your final design must have all screens that are required to deliver the functionality.

```html
<!DOCTYPE html>
<html lang="en">
<head>
<meta charset="utf-8">
<title>TaskOra – Client Contact</title>
<link rel="stylesheet" href="https://fonts.googleapis.com/css2?family=Roboto:wght@400;500&display=swap">
<style>
  :root {
    --hero-dark: #4a3434;
    --hero-mid: #8c6a62;
    --hero-light: #c9a38f;
    --bg-rose: #d8746a;
    --bg-peach: #e8a07a;
    --bg-yellow: #e6d788;
    --bg-plum: #9a5560;
    --accent-green: #5aaf83;
    --accent-blue: #3d55b0;
    --accent-cyan: #6fdcf5;
    --badge-red: #e0302e;
    --tab-cream: rgba(244, 232, 200, 0.93);
    --field-fill: rgba(255, 240, 232, 0.62);
    --field-line: rgba(255, 255, 255, 0.55);
    --field-text: #6b6262;
    --icon-ink: #6e6a6a;
    --white: #ffffff;
  }
  * { box-sizing: border-box; margin: 0; padding: 0; }
  html, body { width: 1200px; height: 900px; overflow: hidden; }
  body { font-family: 'Roboto', sans-serif; position: relative; background: var(--bg-peach); }

  .backdrop {
    position: absolute; inset: 0;
    background:
      radial-gradient(ellipse 420px 300px at 1050px 520px, var(--bg-yellow), transparent 70%),
      radial-gradient(ellipse 380px 260px at 260px 520px, var(--bg-rose), transparent 75%),
      radial-gradient(ellipse 500px 220px at 200px 880px, var(--bg-plum), transparent 75%),
      radial-gradient(ellipse 500px 300px at 900px 850px, #e38a6c, transparent 75%),
      linear-gradient(120deg, #d98572 0%, #e59a78 45%, #e8c27f 75%, #e6d08a 100%);
  }
  .hero {
    position: absolute; left: 0; top: 0; width: 1200px; height: 251px;
    background:
      radial-gradient(ellipse 260px 200px at 560px 230px, #b77a72, transparent 75%),
      radial-gradient(ellipse 300px 200px at 420px 60px, var(--hero-dark), transparent 75%),
      radial-gradient(ellipse 260px 240px at 160px 120px, var(--hero-light), transparent 75%),
      linear-gradient(90deg, #c29884 0%, #6b4a44 35%, #5a3c3a 55%, #3e2c2e 80%, #35282a 100%);
  }

  .status-bar {
    position: absolute; top: 0; left: 0; width: 1200px; height: 38px;
    color: var(--white); font-size: 17px; display: flex; align-items: center; justify-content: space-between;
    padding: 0 18px;
  }
  .status-left, .status-right { display: flex; align-items: center; gap: 6px; width: 200px; }
  .status-right { justify-content: flex-end; }
  .status-time { font-weight: 500; }
  .battery { width: 36px; height: 15px; border: 1.5px solid var(--white); border-radius: 3px; padding: 1.5px; position: relative; }
  .battery::before { content: ""; display: block; width: 100%; height: 100%; background: var(--white); border-radius: 1px; }
  .battery::after { content: ""; position: absolute; right: -4px; top: 4px; width: 2px; height: 5px; background: var(--white); }

  .profile { position: absolute; left: 0; top: 55px; width: 1200px; text-align: center; }
  .avatar {
    width: 112px; height: 112px; border-radius: 50%; margin: 0 auto;
    background: radial-gradient(circle at 50% 45%, #c99580 0%, #7a5043 55%, #3a2723 100%);
    position: relative;
  }
  .avatar-edit {
    position: absolute; right: 0; top: 14px; width: 22px; height: 22px; border-radius: 50%;
    background: var(--badge-red); border: 2px solid var(--white);
    display: flex; align-items: center; justify-content: center;
  }
  .profile-name { color: var(--white); font-size: 20.5px; margin-top: 10px; }
  .profile-phone { color: var(--accent-cyan); font-size: 16px; margin-top: 6px; letter-spacing: 0.3px; }

  .update-btn {
    position: absolute; left: 1005px; top: 182px; width: 168px; height: 43px;
    background: var(--accent-blue); color: var(--white); border-radius: 2px;
    font-size: 15.5px; letter-spacing: 0.5px; display: flex; align-items: center; justify-content: center; gap: 14px;
    box-shadow: 0 2px 3px rgba(0,0,0,0.25);
  }

  .tabs { position: absolute; left: 0; top: 251px; width: 1200px; height: 62px; display: flex; z-index: 2; }
  .tab {
    flex: 1; display: flex; align-items: center; justify-content: center; gap: 12px;
    background: var(--tab-cream); color: #555; font-size: 21px; border-left: 1px solid rgba(255,255,255,0.6);
  }
  .tab:first-child { border-left: none; }
  .tab.is-active { background: var(--accent-green); color: var(--white); }

  .form { position: absolute; left: 0; top: 0; width: 1200px; height: 900px; }
  .field {
    position: absolute; height: 62px; background: var(--field-fill);
    border: 1px solid var(--field-line); display: flex; align-items: center;
    color: var(--field-text); font-size: 18px; box-shadow: 0 1px 2px rgba(120,60,50,0.12);
  }
  .field-icon {
    width: 78px; height: 44px; display: flex; align-items: center; justify-content: center;
    border-right: 1px solid rgba(255,255,255,0.7);
  }
  .field-label { padding-left: 20px; }
  .section-title { position: absolute; left: 20px; top: 462px; color: var(--white); font-size: 21px; }
  svg.ico { stroke: var(--icon-ink); fill: none; stroke-width: 1.4; }
</style>
</head>
<body>
  <div class="backdrop" role="img" aria-label="Softly blurred warm backdrop photo in rose, peach and yellow tones"></div>
  <div class="hero" role="img" aria-label="Blurred enlarged client portrait photo behind the header"></div>

  <header class="status-bar">
    <div class="status-left">
      <span>Tablet</span>
      <svg width="18" height="14" viewBox="0 0 18 14" fill="none" stroke="#fff" stroke-width="2"><path d="M1 5a11 11 0 0 1 16 0"/><path d="M4 8a7 7 0 0 1 10 0"/><circle cx="9" cy="12" r="1.3" fill="#fff" stroke="none"/></svg>
    </div>
    <div class="status-time">4:21 PM</div>
    <div class="status-right"><span>100%</span><span class="battery"></span></div>
  </header>

  <section class="profile">
    <div class="avatar" role="img" aria-label="Client profile photo">
      <span class="avatar-edit"><svg width="10" height="10" viewBox="0 0 10 10"><path d="M1 9l1-3 5-5 2 2-5 5z" fill="#fff"/></svg></span>
    </div>
    <div class="profile-name">Mara Elden</div>
    <div class="profile-phone">04 120 555 0187</div>
  </section>

  <div class="update-btn">UPDATE
    <svg width="24" height="24" viewBox="0 0 24 24" fill="none" stroke="#fff" stroke-width="2"><path d="M10 3a9 9 0 0 0 0 18"/><path d="M14 21a9 9 0 0 0 0-18"/><path d="M7 3h4v4"/><path d="M17 21h-4v-4"/></svg>
  </div>

  <main class="form">
    <div class="field" style="left:18px;top:263px;width:575px;"></div>
    <div class="field" style="left:611px;top:263px;width:573px;"></div>

    <div class="field" style="left:18px;top:339px;width:377px;">
      <span class="field-icon"><svg class="ico" width="26" height="18" viewBox="0 0 26 18"><rect x="1" y="1" width="24" height="16"/><path d="M1 1l12 9 12-9M1 17l9-8M25 17l-9-8"/></svg></span><span class="field-label">Email</span></div>
    <div class="field" style="left:411px;top:339px;width:378px;">
      <span class="field-icon"><svg class="ico" width="14" height="24" viewBox="0 0 14 24"><rect x="1" y="1" width="12" height="22" rx="2"/><path d="M1 5h12M1 19h12"/></svg></span><span class="field-label">Mobile</span></div>
    <div class="field" style="left:805px;top:339px;width:377px;">
      <span class="field-icon"><svg class="ico" width="24" height="24" viewBox="0 0 24 24"><path d="M5 2l4 5-2 2c1 3 4 6 7 7l2-2 5 4-2 3C11 21 3 13 2 5z"/><path d="M14 2a8 8 0 0 1 8 8M14 6a4 4 0 0 1 4 4"/></svg></span><span class="field-label">Landline</span></div>

    <h2 class="section-title" style="font-weight:400;">Emergency Contact</h2>

    <div class="field" style="left:18px;top:511px;width:377px;">
      <span class="field-icon"><svg class="ico" width="24" height="26" viewBox="0 0 24 26"><circle cx="12" cy="8" r="6"/><path d="M1 25c0-6 5-10 11-10s11 4 11 10z"/></svg></span><span class="field-label">First Name</span></div>
    <div class="field" style="left:411px;top:511px;width:378px;">
      <span class="field-icon"><svg class="ico" width="24" height="26" viewBox="0 0 24 26"><circle cx="12" cy="8" r="6"/><path d="M1 25c0-6 5-10 11-10s11 4 11 10z"/></svg></span><span class="field-label">Last Name</span></div>
    <div class="field" style="left:805px;top:511px;width:377px;">
      <span class="field-icon"><svg class="ico" width="22" height="26" viewBox="0 0 22 26"><path d="M11 2v5M3 12h16v12H3zM1 24h20M3 16c3 2 5-2 8 0s5 2 8 0"/><rect x="8" y="7" width="6" height="5"/></svg></span><span class="field-label">Year of Birth</span></div>

    <div class="field" style="left:18px;top:587px;width:1166px;">
      <span class="field-icon"><svg class="ico" width="28" height="26" viewBox="0 0 28 26"><path d="M14 17s-6-6-6-10a6 6 0 0 1 12 0c0 4-6 10-6 10z"/><circle cx="14" cy="7" r="2"/><path d="M8 15H2v10h24V15h-6"/></svg></span><span class="field-label">Address</span></div>

    <div class="field" style="left:18px;top:663px;width:575px;">
      <span class="field-icon"><svg width="20" height="18" viewBox="0 0 20 18" fill="#6e6a6a"><rect x="1" y="1" width="5" height="5"/><rect x="7" y="7" width="5" height="5"/><rect x="14" y="12" width="5" height="5"/></svg></span><span class="field-label">Suburb</span></div>
    <div class="field" style="left:611px;top:663px;width:573px;">
      <span class="field-icon"><svg width="30" height="18" viewBox="0 0 30 18"><rect x="1" y="1" width="28" height="16" rx="3" fill="none" stroke="#6e6a6a" stroke-width="1.4"/><text x="15" y="13" text-anchor="middle" font-family="Roboto, sans-serif" font-size="10" fill="#6e6a6a">ZIP</text></svg></span><span class="field-label">Post Code</span></div>

    <div class="field" style="left:18px;top:740px;width:377px;">
      <span class="field-icon"><svg class="ico" width="26" height="18" viewBox="0 0 26 18"><rect x="1" y="1" width="24" height="16"/><path d="M1 1l12 9 12-9M1 17l9-8M25 17l-9-8"/></svg></span><span class="field-label">Email</span></div>
    <div class="field" style="left:411px;top:740px;width:378px;">
      <span class="field-icon"><svg class="ico" width="14" height="24" viewBox="0 0 14 24"><rect x="1" y="1" width="12" height="22" rx="2"/><path d="M1 5h12M1 19h12"/></svg></span><span class="field-label">Mobile</span></div>
    <div class="field" style="left:805px;top:740px;width:377px;">
      <span class="field-icon"><svg class="ico" width="24" height="24" viewBox="0 0 24 24"><path d="M5 2l4 5-2 2c1 3 4 6 7 7l2-2 5 4-2 3C11 21 3 13 2 5z"/><path d="M14 2a8 8 0 0 1 8 8M14 6a4 4 0 0 1 4 4"/></svg></span><span class="field-label">Landline</span></div>

    <div class="field" style="left:18px;top:816px;width:1166px;">
      <span class="field-icon"><svg class="ico" width="26" height="26" viewBox="0 0 26 26"><circle cx="12" cy="5" r="2.5"/><path d="M6 12l5-4 4 4-2 5 4 6M11 17l-5 6M15 12l4 1"/><circle cx="21" cy="5" r="3"/><path d="M21 3.5V5h1"/></svg></span><span class="field-label">Work</span></div>
  </main>

  <nav class="tabs">
    <div class="tab is-active">
      <svg width="20" height="16" viewBox="0 0 20 16" fill="none" stroke="#fff" stroke-width="1.5"><rect x="1" y="1" width="18" height="14"/><path d="M4 5h4v5H4zM10 5h6M10 8h6M10 11h6"/></svg>Contact</div>
    <div class="tab">
      <svg width="22" height="22" viewBox="0 0 22 22" fill="none" stroke="#555" stroke-width="1.5"><path d="M19 11a8 8 0 1 1-3-6.2"/><path d="M17 2v3h-3"/><text x="11" y="14" text-anchor="middle" font-family="Roboto, sans-serif" font-size="7" fill="#555" stroke="none">24</text></svg>Service</div>
    <div class="tab">
      <svg width="10" height="20" viewBox="0 0 10 20"><rect x="1" y="1" width="8" height="18" rx="1" fill="#555"/><circle cx="5" cy="6" r="1.5" fill="#f4e8c8"/><circle cx="5" cy="11" r="1.5" fill="#f4e8c8"/><circle cx="5" cy="15" r="1.2" fill="#f4e8c8"/></svg>Permission</div>
    <div class="tab">
      <svg width="22" height="18" viewBox="0 0 22 18" fill="none" stroke="#555" stroke-width="1.5"><path d="M1 1v16h20"/><path d="M5 16V10M9 16V7M13 16V11M17 16V5"/><path d="M4 8l5-4 4 4 6-6"/></svg>Financial</div>
  </nav>
</body>
</html>
```